Stonebrace Business Card Design

The Stonebrace Co is an aggregate (crushing) equipment dealer serving Western Canadian provinces. Stonebrace is a distributor of aggregate equipment for different manufacturers.

We are looking to change and update the existing business card which has been used since the existence of the company. A copy of existing card has been attached for reference. The Stonebrace Co logo we want to remain the same and we want the green color to remain the same.

We are wanting something new with a different look. A refreshing card to show a new modern and updated look. No longer wanting to have the manufacturers on the back of the card but something more like our logo on the back of the card with a statement like "Crushing Solutions"

ideas could be:
- card can be different colors on front and back
- front or reverse of the card could possibly be the green color with the logo in black

Target Market(s)

Owners of Aggregate/Crushing companies

Contact Information for Business Card

see above

Requirements
Must have
• - logo to remain same along with same font within logo
• - green color to remain same
Nice to have
• as noted above under project description
Should not have

```html
<!DOCTYPE html>
<html lang="en">
<head>
<meta charset="utf-8">
<title>Stonebrace Business Card</title>
<link rel="stylesheet" href="https://fonts.googleapis.com/css2?family=Arimo:wght@400;700&display=swap">
<style>
  :root {
    --brand-green: #85870f;
    --ink: #1e1e1e;
    --text: #2e2e2e;
    --card: #ffffff;
    --backdrop: #e9e7e4;
  }
  * { margin: 0; padding: 0; box-sizing: border-box; }
  html, body { width: 1200px; height: 900px; overflow: hidden; }
  body {
    position: relative;
    background: var(--backdrop);
    font-family: "Arimo", Arial, sans-serif;
    color: var(--text);
  }
  .card {
    position: absolute;
    background: var(--card);
    box-shadow: 0 4px 18px rgba(0,0,0,0.12);
  }
  .card-front { left: 150px; top: 80px; width: 588px; height: 363px; }
  .card-back  { left: 388px; top: 505px; width: 567px; height: 352px; }

  .front-brand {
    position: absolute; left: 62px; top: 150px;
    display: flex; align-items: center; gap: 8px;
  }
  .brand-dot { width: 14px; height: 14px; border-radius: 50%; background: var(--brand-green); }
  .front-brand .brand-name { font-size: 21px; font-weight: 700; color: var(--brand-green); }

  .contact-name {
    position: absolute; left: 254px; top: 66px;
    font-size: 21px; font-weight: 400; letter-spacing: 0.5px;
    color: var(--brand-green);
  }
  .contact-list {
    position: absolute; left: 258px; top: 114px;
    list-style: none; font-size: 16px; line-height: 21.5px;
  }
  .contact-list li { display: flex; align-items: center; gap: 5px; }
  .contact-list svg { width: 14px; height: 12px; fill: var(--brand-green); flex: none; }
  .company-address {
    position: absolute; left: 258px; top: 242px;
    font-size: 16px; line-height: 21.5px; font-style: normal;
  }
  .company-address strong { font-weight: 700; }

  .back-brand {
    position: absolute; left: 0; right: 0; top: 190px;
    display: flex; justify-content: center; align-items: center; gap: 12px;
  }
  .back-brand .brand-dot { width: 20px; height: 20px; }
  .back-brand .brand-name {
    font-size: 24px; font-weight: 700; letter-spacing: 0.5px;
    text-transform: uppercase; color: var(--ink);
  }
  .tagline {
    position: absolute; left: 38px; right: 38px; top: 266px;
    display: flex; align-items: center; gap: 10px;
    font-size: 16px; font-weight: 700; letter-spacing: 0.5px;
    color: #3a3a3a; white-space: nowrap;
  }
  .tagline::before, .tagline::after {
    content: ""; flex: 1; height: 1.5px; background: var(--brand-green);
  }
</style>
</head>
<body>
  <section class="card card-front" aria-label="Business card front">
    <div class="front-brand">
      <span class="brand-dot"></span>
      <span class="brand-name">Stonebrace</span>
    </div>
    <h1 class="contact-name">DEREK MALVERN</h1>
    <ul class="contact-list">
      <li><svg viewBox="0 0 14 12"><path d="M1 3c3-3 9-3 12 0v2h-3V3.5H4V5H1z M3 6h8l2 5H1z"/></svg>780.555.0142(Direct)</li>
      <li><svg viewBox="0 0 14 12"><path d="M1 3c3-3 9-3 12 0v2h-3V3.5H4V5H1z M3 6h8l2 5H1z"/></svg>780.555.0178</li>
      <li><svg viewBox="0 0 14 12"><path d="M4 0h6v4H4z M1 4h12v8H1z"/></svg>780.555.0193</li>
      <li><svg viewBox="0 0 14 12"><path d="M1 2h12v1L7 7 1 3z M1 4.5l6 4 6-4V10H1z"/></svg>derek@stonebr.com</li>
      <li><svg viewBox="0 0 14 12"><circle cx="7" cy="6" r="6"/></svg>www.stonebrace.ca</li>
    </ul>
    <address class="company-address">
      <strong>The Stonebrace Co.</strong><br>
      2290-48B Street<br>
      Camrose, Alberta T4V 1K6
    </address>
  </section>

  <section class="card card-back" aria-label="Business card back">
    <div class="back-brand">
      <span class="brand-dot"></span>
      <span class="brand-name">The Stonebrace Co.</span>
    </div>
    <p class="tagline">CRUSHING SOLUTIONS</p>
  </section>
</body>
</html>
```